Consulting company requires a logo and business card design

I require a logo/business card design for a new company based in Sexsmith Alberta called TallMarsh Integrity Consulting Ltd. I plan to provide the following services: Construction management/inspection for the oil and gas industry, as well as general consulting for Asset Management, fleet management, etc. Have attached a copy of resume for use as guide for

Target Market(s)

Businesses within the oil and gas production, construction and shipping industry

Industry/Entity Type

Oil And Gas

Contact Information for Business Card

Believe should highlight, services offered, safety, quality,

Logo Text

TallMarsh Integrity Consulting (TMIC) ?

Font styles to use
Script

Requirements
Must have
• Open to all options

```html
<!DOCTYPE html>
<html lang="en">
<head>
<meta charset="utf-8">
<title>TallMarsh Integrity Consulting Ltd – Business Card</title>
<link rel="stylesheet" href="https://fonts.googleapis.com/css2?family=Lato:wght@700&family=Source+Sans+3:wght@400;600&display=swap">
<style>
  :root {
    --backdrop: #000000;
    --card-light: #e9eaeb;
    --brand-red: #c41b3e;
    --text-grey: #3f3f42;
    --white: #ffffff;
  }
  html, body {
    margin: 0;
    padding: 0;
    width: 1200px;
    height: 900px;
    overflow: hidden;
    background: var(--backdrop);
  }
  .stage {
    position: relative;
    width: 1200px;
    height: 900px;
  }
  .card {
    position: absolute;
    top: 200px;
    width: 310px;
    height: 502px;
    box-sizing: border-box;
    overflow: hidden;
  }
  .card--front {
    left: 265px;
    background: var(--card-light);
    border-radius: 52px 0 52px 0;
  }
  .card--back {
    left: 641px;
    background: var(--brand-red);
    border-radius: 0 55px 0 55px;
  }
  .brand-mark {
    position: absolute;
    left: 115px;
    top: 50px;
    width: 80px;
    height: 80px;
    border-radius: 50%;
    background: var(--brand-red);
  }
  .brand-name {
    position: absolute;
    left: 0;
    width: 100%;
    margin: 0;
    text-align: center;
    font-family: "Lato", sans-serif;
    font-weight: 700;
    font-size: 25px;
    line-height: 28px;
  }
  .card--front .brand-name {
    top: 146px;
    color: var(--brand-red);
  }
  .card--back .brand-name {
    top: 405px;
    color: var(--white);
  }
  .contact {
    position: absolute;
    left: 27px;
    top: 326px;
    font-family: "Source Sans 3", sans-serif;
    color: var(--text-grey);
  }
  .contact__name {
    margin: 0;
    font-weight: 600;
    font-size: 18px;
    line-height: 22px;
    letter-spacing: 0.3px;
    color: var(--brand-red);
  }
  .contact__role {
    margin: 1px 0 0;
    font-size: 14px;
    line-height: 18px;
  }
  .contact__address {
    margin: 16px 0 0;
    font-style: normal;
    font-size: 14px;
    line-height: 16px;
  }
  .contact__lines {
    list-style: none;
    margin: 11px 0 0;
    padding: 0;
    font-size: 14px;
    line-height: 19px;
  }
  .contact__lines li {
    display: flex;
    align-items: center;
    gap: 6px;
  }
  .contact__icon {
    width: 10px;
    height: 10px;
    fill: var(--brand-red);
  }
</style>
</head>
<body>
<main class="stage">
  <section class="card card--front" aria-label="Business card front">
    <div class="brand-mark" aria-hidden="true"></div>
    <h1 class="brand-name">TallMarsh Integrity<br>Consulting Ltd</h1>
    <div class="contact">
      <p class="contact__name">DANA WHITFIELD</p>
      <p class="contact__role">Managing Director</p>
      <address class="contact__address">4821, Meadow Ridge Road<br>Region Name, 654321</address>
      <ul class="contact__lines">
        <li>
          <svg class="contact__icon" viewBox="0 0 10 10" aria-hidden="true"><path d="M1 3.2C1 2 2 1.2 5 1.2S9 2 9 3.2V4H7V3H3v1H1z M2.2 5 3.5 3.8h3L7.8 5V9H2.2z M5 5.6a1.2 1.2 0 1 0 0 2.4a1.2 1.2 0 1 0 0-2.4z"/></svg>
          <span>780-555-0142</span>
        </li>
        <li>
          <svg class="contact__icon" viewBox="0 0 10 10" aria-hidden="true"><path d="M0.5 2h9v6h-9z M1.2 2.6 5 5.6 8.8 2.6" stroke="#e9eaeb" stroke-width="0.8"/></svg>
          <span>info@tallmarshic.com</span>
        </li>
      </ul>
    </div>
  </section>

  <section class="card card--back" aria-label="Business card back">
    <h2 class="brand-name">TallMarsh Integrity<br>Consulting Ltd</h2>
  </section>
</main>
</body>
</html>
```